Lotstallmart.com Webpage Design

Design Brief for lotstallmart.com (Copy of Brief also in attached Word file)

Name of Website- lotstallmart.com (existing logo and look & feel of website to be changed)

Logo - Finalised. The logo files are attached with the brief as “logo.jpeg”. The “Blue- Grey” version of the logo is for use on lighter backgrounds and the “Orange-White” version of the logo is for use on darker backgrounds. (A full Black version of the logo is also attached). Both versions may be used in different parts of the website. All attached files are in .png format.
Status - The website in functional and is undergoing user trials. However, we want to improve the look & feel of the website so at it seems
a. cotemporary,
b. Easy to Navigate
c. professional and
d. Vibrant.

Please visit ‘lotstallmart.com’ to check out the website and its functionalities – please use it only as a reference for the features & functions to be provided, however the designer should use a ‘Free Hand’ in designing the composition of various parts of the webpage without getting too influenced by the existing design

Objective of the Website ‘lotstallmart.com –
a. It is a portal focussed on listing of ‘Retail’ specific real-estate properties by developers, owners and realty brokers. The properties shall listed under the following four categories-
i. Retail Malls
ii. Shopping Complexes
iii. High-street shops
iv. Retail Warehouses
*refer lotstallmart.com for better clarity

b. The abovementioned properties shall be listed either for ‘Sale’ or ‘rent\lease’ or both

c. Users shall visit the site in case they wish to acquire a retail \ shop space either on ‘sale’ or ‘rent’. These Users would be able to specify the ‘Search Criteria’ through the tool-bars provided on the website – the ‘Search Criteria’ shall comprise of ‘Type of space category’, ‘City’, ‘Locality’, transaction type ie ‘Rent \ Sale’ and ‘Area Range’

d. The main revenue model for the website shall be listing fee ( or advertising charges ) payable by those listing their properties on the website.

Three Main Pages of Website (lotstallmart.com) that need to be designed -
a. Main Home Page (visit the web link - http://lotstallmart.com/ ) - The main home page has the “Search Toolbar” for specifying of Search Criteria by the User. It shall also have the following features & functions-
i. Main Advertising Banner
ii. Featured Projects
iii. New Launches
iv. Toolbar with buttons – ‘Advertise with Us’, ‘Listings Alert’, ‘Mart Wizards’, ‘Advertiser Login’

b. Property Listings Page (visit the web link - http://lotstallmart.com/gurgaon-in-india ) - The List of property options that match the Criteria specified by the ‘User’ get displayed on this page.

c. Property Detail Page - When the ‘User’ clicks on the “More….” Button on the ‘Property Listings Page’ (given in point b. above) the web page with the details of the property opens. (For Example – visit the web link - http://lotstallmart.com/vorne-Shopping-Complex-vorne-quadrion-gurgaon-636 )

Note:- Please refer to attached ‘Shopping’ related images the designer may use them on the website to provide a look & feel of retail if required – either separately or rotate in a single window

Target Market(s)

Retailers & Investors looking for retail space, Real Estate Brokers, Developers

Industry/Entity Type

Advertising

Number of Pages Required

3 page

Requirements
Must have
• Refer to existing site lotstallmart.com -- all the existing functionalities are a must have.
Nice to have
• The Designer may use the retail related images on the website if required for making it more vibrant. Refer attached images Shopping(1-6).jpg

```html
<!DOCTYPE html>
<html lang="en">
<head>
<meta charset="utf-8">
<title>Lotstallmart.com – Retail Space Portal</title>
<link href="https://fonts.googleapis.com/css2?family=Open+Sans:wght@400;600;700&family=Montserrat:wght@400;700&display=swap" rel="stylesheet">
<style>
:root{
  --blue:#0a84d6;
  --blue-dark:#0770bb;
  --orange:#d4850f;
  --orange-text:#e1920f;
  --ink:#1d1d1d;
  --header:#1f1f1f;
  --dark:#1c1c1c;
  --grey-bg:#eeeeee;
  --body:#444;
  --muted:#666;
  --white:#fff;
}
*{box-sizing:border-box;margin:0;padding:0}
html,body{width:1200px;height:2691px;overflow:hidden}
body{font-family:"Open Sans",Arial,sans-serif;color:var(--body);background:var(--white);position:relative}
section,header,footer,nav{position:absolute;left:0;width:1200px}
.abs{position:absolute}

/* city bar */
.city-bar{top:0;height:40px;background:var(--blue);display:flex;justify-content:center;align-items:center;font-size:14px;color:var(--white);font-weight:600}
.city-bar span{padding:0 11px;border-right:1px solid rgba(255,255,255,.6);line-height:14px}
.city-bar span:last-child{border:none}

/* header */
.site-header{top:40px;height:130px;background:var(--header);color:var(--white)}
.brand{left:111px;top:32px;display:flex;align-items:center;gap:10px}
.brand-dot{width:34px;height:34px;border-radius:50%;background:var(--blue)}
.brand-name{font-size:33px;font-weight:700;color:var(--white);letter-spacing:-.5px}
.brand-tag{left:157px;top:76px;font-size:9px;font-weight:700;color:#bbb;letter-spacing:.6px}
.nav-item{top:42px;font-size:16px;line-height:20px}
.nav-item small{display:block;font-size:12px;color:#ddd}
.home-icon{left:433px;top:50px}
.listing-note{left:924px;top:20px;font-size:12px;color:#ddd}
.btn-login{left:920px;top:44px;width:169px;height:42px;background:var(--orange);color:var(--white);font-weight:700;font-size:16px;display:flex;align-items:center;justify-content:center;border-radius:2px}
.register-note{left:927px;top:92px;font-size:12px;color:var(--orange-text)}

/* hero */
.hero{top:170px;height:590px;background:
  radial-gradient(ellipse 260px 200px at 740px 150px,#e8c0a4 0%,rgba(232,192,164,0) 70%),
  radial-gradient(ellipse 260px 300px at 890px 330px,#4da3d9 0%,rgba(77,163,217,0) 70%),
  radial-gradient(ellipse 140px 150px at 710px 400px,#2f8fd8 0%,rgba(47,143,216,0) 70%),
  radial-gradient(ellipse 120px 140px at 560px 470px,#e3b52a 0%,rgba(227,181,42,0) 70%),
  radial-gradient(ellipse 120px 130px at 820px 490px,#f0c43a 0%,rgba(240,196,58,0) 70%),
  radial-gradient(ellipse 220px 180px at 180px 120px,#c4553a 0%,rgba(196,85,58,0) 70%),
  radial-gradient(ellipse 200px 160px at 420px 80px,#e89a4a 0%,rgba(232,154,74,0) 70%),
  radial-gradient(ellipse 180px 160px at 1120px 540px,#e0613a 0%,rgba(224,97,58,0) 70%),
  linear-gradient(100deg,#3a2520 0%,#6a3b2c 30%,#8c5a44 50%,#5e6f80 75%,#2b2a2c 100%)}
.hero-title{left:118px;top:165px;font-family:"Montserrat",sans-serif;font-size:41px;line-height:46px;color:var(--white);font-weight:400}
.hero-title b{font-weight:700}
.hero-arrow{top:248px;width:42px;height:42px;border-radius:50%;background:#222;display:flex;align-items:center;justify-content:center}
.search-box{left:109px;top:452px;width:980px;height:138px;background:var(--orange);border-radius:2px;color:var(--white)}
.search-title{left:22px;top:24px;font-size:21px;font-weight:700;letter-spacing:.2px}
.check{font-size:12px;display:flex;align-items:center;gap:6px}
.check i{width:12px;height:12px;background:var(--white);display:inline-block}
.field-label{font-size:13px}
.select{height:26px;background:var(--white);color:#333;font-size:12px;padding:0 8px;display:flex;align-items:center;justify-content:space-between}
.select::after{content:"";border:5px solid transparent;border-top:6px solid #222;margin-top:5px}
.btn-search{left:793px;top:54px;width:169px;height:42px;background:var(--blue);font-weight:700;font-size:17px;display:flex;align-items:center;justify-content:center}

/* categories */
.categories{top:760px;height:280px;background:var(--white)}
.category{width:250px;text-align:center;top:40px}
.category-photo{width:140px;height:140px;border-radius:50%;margin:0 auto;border:5px solid #fff;box-shadow:0 0 0 1px #ccc}
.category h3{margin-top:20px;font-size:19px;font-weight:400;color:var(--orange-text)}
.category p{font-size:14px;color:var(--muted);margin-top:2px}

/* project rows */
.featured{top:1040px;height:431px;background:radial-gradient(ellipse 700px 300px at 900px 60px,#4a4a4a,rgba(74,74,74,0) 70%),linear-gradient(135deg,#2e2e2e,#161616 55%,#262626)}
.launches{top:1471px;height:407px;background:var(--white)}
.row-title{left:127px;font-size:23px;font-weight:400}
.row-title span{font-size:16px;margin-left:22px}
.featured .row-title{top:42px;color:var(--white)}
.featured .row-title span{color:#aaa}
.launches .row-title{top:38px;color:var(--ink)}
.launches .row-title span{color:#777}
.pager{display:flex;gap:3px}
.pager i{width:20px;height:20px;border-radius:50%;display:block}
.card{width:219px}
.card-photo{height:152px;position:relative}
.card-city{position:absolute;left:0;bottom:15px;padding:2px 10px;color:var(--white);font-size:14px}
.card-body{height:120px;color:var(--white);text-align:center;font-size:15px;font-weight:600;line-height:22px;padding-top:8px}
.card-body a{display:block;margin-top:8px;padding-top:6px;border-top:1px solid rgba(255,255,255,.35);text-decoration:underline;color:var(--white);font-size:15px;font-weight:700}
.featured .card-city{background:var(--orange)}
.featured .card-body{background:var(--blue)}
.launches .card-body{background:var(--orange)}
.launches .card-city{background:var(--blue)}
.photo-surat{background:linear-gradient(160deg,#c9d2c4 0%,#7f9a86 35%,#5d6f66 60%,#a7b3a4 100%)}
.photo-faridabad{background:radial-gradient(ellipse 80px 110px at 90px 90px,#f1ece2,rgba(241,236,226,0) 70%),linear-gradient(180deg,#1f3f8a 0%,#3f63b0 45%,#a4a29a 80%,#5a5750 100%)}
.photo-gurgaon{background:radial-gradient(ellipse 90px 70px at 150px 90px,#d8b08a,rgba(216,176,138,0) 70%),linear-gradient(180deg,#b7a4c2 0%,#d7a9a2 40%,#8e7a6e 75%,#6a5c52 100%)}
.photo-delhi{background:radial-gradient(ellipse 45px 110px at 60px 100px,#f0b540,rgba(240,181,64,0) 70%),radial-gradient(ellipse 120px 40px at 110px 140px,#d8862a,rgba(216,134,42,0) 70%),linear-gradient(180deg,#1e2c52 0%,#384c78 45%,#7a5a3a 85%,#3a2a20 100%)}

/* info */
.info{top:1878px;height:429px;background:var(--grey-bg);border-top:1px solid #ddd}
.col{top:38px;width:290px}
.col h2{font-size:23px;font-weight:400;color:var(--ink);margin-bottom:22px}
.col p{font-size:14.5px;line-height:21px;color:#333}
.input{height:32px;background:var(--white);border:1px solid #ccc;font-size:12px;color:#555;padding:0 12px;display:flex;align-items:center;justify-content:space-between;margin-bottom:10px}
.hint{font-size:12px;color:#333;margin:-6px 0 10px}
.btn-blue{display:inline-flex;width:143px;height:36px;background:var(--blue);color:var(--white);font-weight:700;font-size:15px;align-items:center;justify-content:center;border-radius:2px}
.btn-blue.small{width:85px}

/* footer */
.site-footer{top:2307px;height:384px;background:var(--dark);color:#ccc}
.site-footer h2{font-size:22px;font-weight:400;color:var(--white)}
.links{font-size:13px;line-height:25px;list-style:none}
.links li::before{content:"•";margin-right:8px}
.about-text{font-size:12.5px;line-height:25px}
.about-text a{color:var(--blue)}
.contact-line{font-size:13px;line-height:23px;display:flex;gap:12px}
.social{display:flex;gap:4px}
.social i{width:22px;height:22px;background:#3b6fc4;display:block}
.footer-rule{left:124px;top:298px;width:952px;height:1px;background:#3a3a3a}
.copyright{left:124px;top:328px;font-size:13px}
.footer-brand{left:888px;top:318px;display:flex;align-items:center;gap:8px}
</style>
</head>
<body>

<nav class="city-bar">
  <span>Bangalore</span><span>Chennai</span><span>Greater Noida</span><span>Gurgaon</span><span>Hyderabad</span><span>Jaipur</span><span>Khanna</span><span>Kolkatta</span><span>Mumbai</span><span>Noida</span><span>Pune</span><span>Surat</span>
</nav>

<header class="site-header">
  <div class="brand abs"><span class="brand-dot"></span><span class="brand-name">lotstallmart</span></div>
  <div class="brand-tag abs">INDIA'S LEADING PORTAL FOR RETAIL SPACE</div>
  <svg class="home-icon abs" width="22" height="20" viewBox="0 0 22 20"><path d="M11 1 1 10h3v9h5v-6h4v6h5v-9h3z" fill="#fff"/></svg>
  <div class="nav-item abs" style="left:477px">Advertise With Us<small>Standard listing - FREE</small></div>
  <div class="nav-item abs" style="left:648px">Mart Wizards<small>Shop Search Services</small></div>
  <div class="nav-item abs" style="left:807px;top:54px">Listing Alerts</div>
  <div class="listing-note abs">Listing Your Property Here</div>
  <div class="btn-login abs">ADVERTISE LOGIN</div>
  <div class="register-note abs">New Advertiser - Register</div>
</header>

<section class="hero" role="img" aria-label="Banner photo of a couple shopping with colourful bags in a mall">
  <h1 class="hero-title abs">SHOPS AT <b>COX</b><br><b>TOWN BANGALORE</b></h1>
  <div class="hero-arrow abs" style="left:47px"><svg width="12" height="16"><path d="M9 2 3 8l6 6" stroke="#fff" stroke-width="2.5" fill="none"/></svg></div>
  <div class="hero-arrow abs" style="left:1111px"><svg width="12" height="16"><path d="M3 2l6 6-6 6" stroke="#fff" stroke-width="2.5" fill="none"/></svg></div>

  <form class="search-box abs">
    <div class="search-title abs">SELECT RETAIL FORMAT</div>
    <label class="check abs" style="left:22px;top:72px"><i></i>Retail Malls</label>
    <label class="check abs" style="left:126px;top:72px"><i></i>Shopping Complex</label>
    <label class="check abs" style="left:22px;top:97px"><i></i>High Shops</label>
    <label class="check abs" style="left:126px;top:97px"><i></i>Retail Warehouses</label>

    <div class="field-label abs" style="left:291px;top:12px">Sale or Rent Or Both:</div>
    <div class="select abs" style="left:291px;top:36px;width:228px">Both</div>
    <div class="field-label abs" style="left:291px;top:70px">Select Locality/Micro-Market.</div>
    <div class="select abs" style="left:291px;top:94px;width:228px">Both</div>
    <div class="field-label abs" style="left:533px;top:12px">Select City:</div>
    <div class="select abs" style="left:533px;top:36px;width:230px">--Select--</div>
    <div class="field-label abs" style="left:533px;top:70px">Enter Keywords:</div>
    <div class="select abs" style="left:533px;top:94px;width:230px">--Select--</div>
    <div class="btn-search abs">SEARCH</div>
  </form>
</section>

<section class="categories">
  <div class="category abs" style="left:90px"><div class="category-photo" role="img" aria-label="Photo of a retail mall atrium" style="background:radial-gradient(circle at 50% 35%,#f2efe4 0%,#b9c2b5 30%,#6f8476 60%,#3a4a44 100%)"></div><h3>Retail Malls</h3><p>Centrally Air-Conditioned</p></div>
  <div class="category abs" style="left:341px"><div class="category-photo" role="img" aria-label="Photo of a shopping complex escalator" style="background:radial-gradient(circle at 40% 40%,#fff3dc 0%,#e0c494 30%,#9c7a52 60%,#4a3a2c 100%)"></div><h3>Shopping Complex</h3><p>Non Air-Conditioned Building</p></div>
  <div class="category abs" style="left:593px"><div class="category-photo" role="img" aria-label="Photo of a busy high street with shop signs" style="background:radial-gradient(circle at 35% 30%,#e24b3b 0%,rgba(226,75,59,0) 45%),radial-gradient(circle at 70% 65%,#2fa36a 0%,rgba(47,163,106,0) 45%),linear-gradient(180deg,#2a4a8a,#1a1f36)"></div><h3>High Street Shops</h3><p>Road Facing Retail</p></div>
  <div class="category abs" style="left:844px"><div class="category-photo" role="img" aria-label="Photo of warehouse aisles with shelving" style="background:radial-gradient(circle at 50% 45%,#fff1cc 0%,#e0b46a 30%,#9a6a34 60%,#4a3218 100%)"></div><h3>Retail Warehouses</h3><p>Back-end Ratail Storage</p></div>
</section>

<section class="featured">
  <h2 class="row-title abs">Featured Retail Projects <span>Across India</span></h2>
  <div class="pager abs" style="left:1025px;top:48px"><i style="background:#555"></i><i style="background:#555"></i></div>
  <article class="card abs" style="left:127px;top:105px"><div class="card-photo photo-surat" role="img" aria-label="Aerial render of a shopping complex"><span class="card-city">Surat</span></div><div class="card-body">Kestrin<br>Vale<br>Shopping Complex<a>VIEW LISTINGS</a></div></article>
  <article class="card abs" style="left:367px;top:105px"><div class="card-photo photo-faridabad" role="img" aria-label="Render of a tower against a blue sky"><span class="card-city">Faridabad</span></div><div class="card-body">Kestrin<br>Vale<br>Shopping Complex<a>VIEW LISTINGS</a></div></article>
  <article class="card abs" style="left:607px;top:105px"><div class="card-photo photo-gurgaon" role="img" aria-label="City skyline at sunset"><span class="card-city">Guragaon</span></div><div class="card-body">Kestrin<br>Vale<br>Shopping Complex<a>VIEW LISTINGS</a></div></article>
  <article class="card abs" style="left:847px;top:105px"><div class="card-photo photo-delhi" role="img" aria-label="Lit historic building at night"><span class="card-city">New Delhi</span></div><div class="card-body">Kestrin<br>Vale<br>Shopping Complex<a>VIEW LISTINGS</a></div></article>
</section>

<section class="launches">
  <h2 class="row-title abs">Featured New Launches <span>Across India</span></h2>
  <div class="pager abs" style="left:1030px;top:45px"><i style="background:#333"></i><i style="background:#333"></i></div>
  <article class="card abs" style="left:127px;top:95px"><div class="card-photo photo-surat" role="img" aria-label="Aerial render of a shopping complex"><span class="card-city">Surat</span></div><div class="card-body">Kestrin<br>Vale<br>Shopping Complex<a>VIEW LISTINGS</a></div></article>
  <article class="card abs" style="left:367px;top:95px"><div class="card-photo photo-faridabad" role="img" aria-label="Render of a tower against a blue sky"><span class="card-city">Faridabad</span></div><div class="card-body">Kestrin<br>Vale<br>Shopping Complex<a>VIEW LISTINGS</a></div></article>
  <article class="card abs" style="left:607px;top:95px"><div class="card-photo photo-gurgaon" role="img" aria-label="City skyline at sunset"><span class="card-city">Guragaon</span></div><div class="card-body">Kestrin<br>Vale<br>Shopping Complex<a>VIEW LISTINGS</a></div></article>
  <article class="card abs" style="left:847px;top:95px"><div class="card-photo photo-delhi" role="img" aria-label="Lit historic building at night"><span class="card-city">New Delhi</span></div><div class="card-body">Kestrin<br>Vale<br>Shopping Complex<a>VIEW LISTINGS</a></div></article>
</section>

<section class="info">
  <div class="col abs" style="left:124px">
    <h2>Listing Alert</h2>
    <div style="display:flex;gap:14px;margin-bottom:16px">
      <svg width="36" height="36" viewBox="0 0 36 36" style="flex:none"><circle cx="18" cy="18" r="17" fill="#1f4f7a"/><path d="M9 13h18v11H9z" fill="#fff"/><path d="M9 13l9 7 9-7" stroke="#1f4f7a" stroke-width="1.5" fill="none"/></svg>
      <p style="width:236px">Suscribe&nbsp; for Fortnightly Email update on New Listings @ Lot-StallMart</p>
    </div>
    <div class="input">Enter your email address</div>
    <div class="input" style="color:var(--blue)">Select Options <span>⇕</span></div>
    <div class="hint">(select retail format of interest)</div>
    <div class="input">Adilabad <span>▾</span></div>
    <div class="hint">(select cities of interest)</div>
    <span class="btn-blue">SUBSCRIBE</span>
  </div>
  <div class="col abs" style="left:452px">
    <h2>Editor’s Choice</h2>
    <div role="img" aria-label="Photo of a family shopping in a mall" style="height:104px;background:radial-gradient(ellipse 60px 50px at 110px 60px,#e84a5a,rgba(232,74,90,0) 70%),radial-gradient(ellipse 70px 60px at 200px 40px,#f0d8a0,rgba(240,216,160,0) 70%),linear-gradient(90deg,#4a2e24,#9a6a4a 45%,#5a3a3a);margin-bottom:10px"></div>
    <p style="font-size:13.5px">A "Select" Listing of Retail Properties Handpicked by our Editors based on their own positive evaluation on parameters &amp; attributes such as Design Concept, Loca-tion, Developer, Success Potential. So Read On to Check Out for yourself ...........</p>
    <span class="btn-blue" style="margin-top:10px">LEARN MORE</span>
  </div>
  <div class="col abs" style="left:786px">
    <h2>Mart Wizards</h2>
    <p style="margin-bottom:8px;font-size:15px">Post your Retail Space requirement with us and our experts shall get back with suitable options and even help you in your transaction. This is a Free Service!</p>
    <div class="input">Enter your email address</div>
    <div class="input">Mobile</div>
    <div class="input" style="height:74px;align-items:flex-start;padding-top:8px">Add Description of Requirement</div>
    <span class="btn-blue small" style="margin-top:4px">SEND</span>
  </div>
</section>

<footer class="site-footer">
  <h2 class="abs" style="left:124px;top:28px">About Lot Stall Mart</h2>
  <ul class="links abs" style="left:124px;top:88px"><li>About Us</li><li>Privacy Policy</li><li>Terms of Use</li><li>Contact Us</li><li>Site Map</li></ul>
  <ul class="links abs" style="left:270px;top:88px"><li>Retail Malls</li><li>Shopping Complex</li><li>High Street Shops</li><li>Retail Warehouses</li></ul>
  <h2 class="abs" style="left:459px;top:28px">Who We Are</h2>
  <p class="about-text abs" style="left:459px;top:86px;width:318px">Lotstallmart.com is a Specialised Web based platform for Retail Space, featuring properties across India under various formats such as Retail Malls, Shopping Complexes, High-street Shops. Also featured are “Retail Warehouses” which provide the logistic back-end for the retail busi-ness. Lotstallmart.com is useful to various category of users as follows- a. Devel <a>More...</a></p>
  <h2 class="abs" style="left:818px;top:28px">Contact Us</h2>
  <div class="contact-line abs" style="left:818px;top:86px;width:270px"><svg width="14" height="20" viewBox="0 0 14 20" style="flex:none;margin-top:2px"><path d="M7 0a7 7 0 0 0-7 7c0 5 7 13 7 13s7-8 7-13a7 7 0 0 0-7-7z" fill="#0a84d6"/><circle cx="7" cy="7" r="2.5" fill="#1c1c1c"/></svg><span>Trade Nexus Unit 406, 4th Floor, Lorem Ipsum is simply, Sector-x, Gurgaon - 122002</span></div>
  <div class="contact-line abs" style="left:818px;top:174px;align-items:center"><svg width="16" height="16" viewBox="0 0 16 16"><path d="M3 1l3 3-2 2c1 2 3 4 5 5l2-2 3 3-2 3C7 15 1 9 1 3z" fill="#0a84d6"/></svg>Phone : 000-000-0000</div>
  <div class="contact-line abs" style="left:818px;top:204px;align-items:center"><svg width="16" height="16" viewBox="0 0 16 16"><rect x="1" y="5" width="14" height="9" fill="#0a84d6"/><rect x="4" y="1" width="8" height="5" fill="#0a84d6"/></svg>Fax : 000 - 000 - 0000</div>
  <div class="social abs" style="left:838px;top:237px"><i></i><i style="background:#3fa9e0"></i><i style="background:#c33"></i><i style="background:#d44a3a"></i><i style="background:#2a6fb0"></i></div>
  <div class="footer-rule abs"></div>
  <div class="copyright abs">Copyright © 2015 Lot Stall Mart. All rights reserved.</div>
  <div class="footer-brand abs"><span style="width:26px;height:26px;border-radius:50%;background:var(--blue);display:block"></span><span style="font-size:24px;font-weight:700;color:var(--white)">lotstallmart</span></div>
</footer>

</body>
</html>
```